Marwick Partners Exit Plan business consultant web site

This website is for a consulting business that helps other businesses with exit plans. Essentially, assists them with the sale of their business. This website should be very professional, almost with a wall street look. I would like a very attractive image on the homepage. Perhaps something that denotes success. Perhaps a picture of palm trees and a beach? I will leave it to you for interpretation.

Across the screen I would like the words "Does your business have an exit plan?"

Below that it should read the following:
Let us help you with a completely impartial, no obligation assessment (button with link to the contact page)

Also, please use logo in a prominent place on the website so it's easily seen.

Target Market(s)

Males 40+

Coding

Coded - Design and coding required

Number of Pages Required

5+ page

Colors

Designer to choose colors to be used in the design.

Requirements
Must have
• The tabs for the homepage on the top should be:
• 1. About us
• 2. Services
• 3. Industries
• 4. Our success
• 5. Contact
Nice to have
• Clean, professional image.
• Please put FB, Chirpline, Linked In - logos at bottom.
• Here are two examples of a website to give you an idea:
• https://notes.quelvarocapital.example/library/why-every-business-owner-should-have-an-exit-plan
Should not have
• nothing whimsical or cartoon like

```html
<!DOCTYPE html>
<html lang="en">
<head>
<meta charset="utf-8">
<title>Marwick Partners — Exit Planning</title>
<link rel="stylesheet" href="https://fonts.googleapis.com/css2?family=Oswald:wght@500;600&family=Open+Sans:wght@400;600;700&family=Cinzel:wght@500&display=swap">
<style>
:root{
  --ink:#111111;
  --black:#0b0b0b;
  --white:#ffffff;
  --paper:#f4f4f4;
  --line:#d9d9d9;
  --grey:#666666;
  --muted:#9a9a9a;
  --sky-top:#e9eef1;
  --sea:#4c8ea3;
  --dark-band:#1b1b1b;
}
*{box-sizing:border-box;margin:0;padding:0}
html,body{width:1200px;height:3404px;overflow:hidden;background:var(--white)}
body{font-family:"Open Sans",Arial,sans-serif;color:var(--ink);position:relative}
.heading{font-family:"Oswald","Arial Narrow",sans-serif;font-weight:600;text-transform:uppercase;letter-spacing:1px}

/* hero */
.hero{position:absolute;left:0;top:0;width:1200px;height:640px;overflow:hidden}
.hero-photo{position:absolute;inset:0;background:linear-gradient(180deg,var(--sky-top) 0%,#dfe7ea 38%,#8fb8c6 52%,var(--sea) 70%,#8a7a66 100%)}
.nav{position:absolute;top:62px;left:0;width:1200px;font-size:15px;font-weight:600;text-transform:uppercase}
.nav a{position:absolute;color:var(--ink);text-decoration:none}
.nav a.active{border-bottom:2px solid var(--ink);padding-bottom:4px}
.nav-rule{position:absolute;top:88px;height:1px;background:var(--ink)}
.brand{position:absolute;left:520px;top:18px;width:160px;text-align:center}
.brand-square{width:56px;height:56px;background:var(--black);margin:0 auto 10px}
.brand-name{font-family:"Cinzel",serif;font-size:19px;color:var(--ink);letter-spacing:1px}
.hero-copy{position:absolute;left:836px;top:206px;width:330px}
.hero-copy h1{font-size:38px;line-height:1.08;color:var(--ink)}
.hero-copy p{margin-top:18px;font-size:15px;line-height:1.35;text-transform:uppercase;letter-spacing:.5px}
.btn{display:inline-block;background:var(--black);color:var(--white);font-size:13px;font-weight:700;text-transform:uppercase;padding:12px 18px;text-decoration:none;letter-spacing:.5px}
.hero-copy .btn{margin-top:26px}
.btn-small{display:inline-block;border:1px solid var(--ink);color:var(--ink);font-size:11px;padding:4px 10px;text-transform:uppercase;text-decoration:none}

/* services */
.services{position:absolute;top:640px;left:0;width:1200px;height:650px;background:var(--paper)}
.section-title{position:absolute;width:1200px;text-align:center;font-size:30px}
.section-title::after{content:"";display:block;width:420px;height:1px;background:currentColor;opacity:.5;margin:14px auto 0}
.services .section-title{top:48px}
.service{position:absolute;width:444px;height:224px;background:var(--white);border:1px solid var(--line);box-shadow:0 2px 6px rgba(0,0,0,.08);padding:28px 28px 0 104px}
.service svg{position:absolute;left:28px;top:30px}
.service h3{font-size:15px;font-weight:700;text-transform:uppercase}
.service p{margin:12px 0 18px;font-size:13px;line-height:1.4;color:var(--grey)}

/* welcome */
.welcome{position:absolute;top:1290px;left:0;width:1200px;height:530px;background:var(--white)}
.welcome-mark{position:absolute;left:188px;top:70px;width:304px;height:290px;background:var(--black);outline:2px solid var(--white);outline-offset:-22px;display:flex;align-items:center;justify-content:center}
.welcome-mark span{font-family:"Cinzel",serif;color:var(--white);font-size:28px;text-align:center;line-height:1.3}
.welcome-copy{position:absolute;left:572px;top:78px;width:460px}
.welcome-copy .eyebrow{font-size:22px;text-transform:uppercase}
.welcome-copy h2{font-size:44px;line-height:1.05}
.welcome-copy p{margin:26px 0 26px;font-size:14px;line-height:1.6;color:var(--grey)}

/* industries */
.industries{position:absolute;top:1820px;left:0;width:1200px;height:580px;background:linear-gradient(180deg,#262626,var(--dark-band))}
.industries .section-title{top:40px;color:var(--white)}
.industry{position:absolute;top:132px;width:222px;height:328px;background:var(--white)}
.industry .photo{height:212px}
.industry h4{margin-top:18px;text-align:center;font-size:13px;font-weight:700;text-transform:uppercase}
.industry p{margin:8px 16px 0;text-align:center;font-size:12px;line-height:1.4;color:var(--grey)}
.industries .btn-light{position:absolute;left:516px;top:502px;background:var(--white);color:var(--ink);font-size:12px;font-weight:700;padding:10px 16px;text-transform:uppercase;text-decoration:none}

/* success */
.success{position:absolute;top:2400px;left:0;width:1200px;height:600px;background:var(--paper)}
.success .section-title{top:64px}
.quote-mark{position:absolute;font-family:Georgia,serif;font-size:120px;color:#c9c9c9;line-height:1}
.testimonials{position:absolute;left:168px;top:152px;width:880px;height:296px;background:var(--white);box-shadow:0 2px 8px rgba(0,0,0,.1)}
.testimonial{position:absolute;top:40px;width:360px}
.testimonial p{font-size:14px;line-height:1.5;color:var(--grey)}
.author{margin-top:26px;display:flex;align-items:center;gap:16px}
.author::before{content:"";width:56px;height:2px;background:var(--ink)}
.author b{display:block;font-size:12px;text-transform:uppercase;color:var(--ink)}
.author small{font-size:11px;color:var(--grey)}
.dots{position:absolute;top:524px;left:0;width:1200px;display:flex;justify-content:center;gap:12px}
.dots i{width:8px;height:8px;border-radius:50%;background:#bdbdbd}
.dots i.on{background:var(--ink)}

/* footer */
.footer{position:absolute;top:2980px;left:0;width:1200px;height:424px;background:var(--black);color:var(--white)}
.footer-edge{position:absolute;top:-20px;left:0}
.footer-mark{position:absolute;left:132px;top:92px;width:168px;height:232px;border:3px solid var(--white);display:flex;align-items:center;justify-content:center}
.footer-mark span{font-family:"Cinzel",serif;font-size:17px;text-align:center;line-height:1.3}
.footer-col{position:absolute;top:92px}
.footer-col h5{font-size:16px;font-weight:700;text-transform:uppercase;letter-spacing:1px;margin-bottom:20px}
.follow-item{display:flex;align-items:center;gap:18px;margin-bottom:22px;font-size:12px;line-height:1.35;text-transform:uppercase}
.follow-item i{width:30px;height:30px;border-radius:50%;background:var(--white)}
.follow-item em{font-style:normal;text-transform:none;color:#cfcfcf}
.menu-list{list-style:none;font-size:13px;line-height:1.6;color:#e6e6e6}
.contact-item{display:flex;gap:16px;align-items:center;margin-bottom:24px;font-size:12px;line-height:1.4}
.contact-item svg{flex:none}
.contact-item b{display:block;font-size:13px}
.copyright{position:absolute;top:384px;width:1200px;text-align:center;font-size:11px;color:var(--muted)}
</style>
</head>
<body>

<header class="hero">
  <div class="hero-photo" role="img" aria-label="Businessman standing at the end of a wooden pier looking out over a calm sea"></div>
  <nav class="nav">
    <a class="active" style="left:226px">Home</a>
    <a style="left:306px">About us</a>
    <a style="left:428px">Services</a>
    <a style="left:684px">Industries</a>
    <a style="left:810px">Our success</a>
    <a style="left:948px">Contact</a>
  </nav>
  <div class="nav-rule" style="left:224px;width:300px"></div>
  <div class="nav-rule" style="left:676px;width:320px"></div>
  <div class="brand">
    <div class="brand-square"></div>
    <div class="brand-name">Marwick Partners</div>
  </div>
  <div class="hero-copy">
    <h1 class="heading">Does your business have an exit plan?</h1>
    <p>Let us help you with a completely impartial, no obligation assessment</p>
    <a class="btn" href="#contact">Contact us</a>
  </div>
</header>

<section class="services">
  <h2 class="section-title heading">Our services</h2>
  <div class="service" style="left:152px;top:144px">
    <svg width="52" height="52" viewBox="0 0 52 52"><rect x="4" y="4" width="44" height="44" rx="6" fill="none" stroke="#111" stroke-width="3"/><circle cx="23" cy="23" r="9" fill="none" stroke="#111" stroke-width="3"/><line x1="30" y1="30" x2="40" y2="40" stroke="#111" stroke-width="4"/></svg>
    <h3>Business analysis</h3>
    <p>Lorem ipsum dolor sit amet, conse ctetur adipiscing elit, sed do eiusmod tempor incididunt ut labore et dolore magna aliqua.</p>
    <a class="btn-small" href="#">Read more</a>
  </div>
  <div class="service" style="left:608px;top:144px">
    <svg width="52" height="52" viewBox="0 0 52 52"><circle cx="26" cy="17" r="10" fill="#111"/><path d="M6 50c2-14 10-20 20-20s18 6 20 20z" fill="#111"/></svg>
    <h3>Customer service</h3>
    <p>Lorem ipsum dolor sit amet, conse ctetur adipiscing elit, sed do eiusmod tempor incididunt ut labore et dolore magna aliqua.</p>
    <a class="btn-small" href="#">Read more</a>
  </div>
  <div class="service" style="left:152px;top:384px">
    <svg width="52" height="52" viewBox="0 0 52 52"><path d="M4 6h28v18H14l-8 7v-7H4z" fill="#111"/><path d="M22 28h26v16h-2v7l-8-7H22z" fill="#111"/></svg>
    <h3>Consultancy services</h3>
    <p>Lorem ipsum dolor sit amet, conse ctetur adipiscing elit, sed do eiusmod tempor incididunt ut labore et dolore magna aliqua.</p>
    <a class="btn-small" href="#">Read more</a>
  </div>
  <div class="service" style="left:608px;top:384px">
    <svg width="52" height="52" viewBox="0 0 52 52"><rect x="18" y="4" width="32" height="24" fill="#111"/><circle cx="10" cy="18" r="6" fill="#111"/><path d="M2 48V30h16v18z" fill="#111"/><line x1="18" y1="36" x2="48" y2="36" stroke="#111" stroke-width="3"/></svg>
    <h3>Executive coaching</h3>
    <p>Lorem ipsum dolor sit amet, conse ctetur adipiscing elit, sed do eiusmod tempor incididunt ut labore et dolore magna aliqua.</p>
    <a class="btn-small" href="#">Read more</a>
  </div>
</section>

<section class="welcome">
  <div class="welcome-mark"><span>Marwick<br>Partners</span></div>
  <div class="welcome-copy">
    <div class="eyebrow heading">Welcome to</div>
    <h2 class="heading">Marwick Partners</h2>
    <p>On the other hand, we denounce with righteous indignation and dislike men who are so beguiled and demoralized by the charms of pleasure of the moment, so blinded by desire, that they cannot foresee the pain and trouble that are bound to ensue; and equal blame belongs to those who fail in their duty through weakness of will, which is the same as saying through shrinking from toil and pain. These cases are perfectly simple.</p>
    <a class="btn" href="#">Read more</a>
  </div>
</section>

<section class="industries">
  <h2 class="section-title heading">Industries</h2>
  <div class="industry" style="left:132px">
    <div class="photo" role="img" aria-label="Business team meeting around a table" style="background:linear-gradient(160deg,#8a8f96,#4a4e55)"></div>
    <h4>Lorem ipsum</h4><p>Lorem ipsum dolor sit amet, conse ctetur adipiscing elit, sed do eiusmod.</p>
  </div>
  <div class="industry" style="left:372px">
    <div class="photo" role="img" aria-label="Hands working with a calculator and financial papers" style="background:linear-gradient(160deg,#d8d8d8,#7d7d7d)"></div>
    <h4>Lorem ipsum</h4><p>Lorem ipsum dolor sit amet, conse ctetur adipiscing elit, sed do eiusmod.</p>
  </div>
  <div class="industry" style="left:612px">
    <div class="photo" role="img" aria-label="Glowing light bulb idea on a dark background" style="background:radial-gradient(circle at 50% 45%,#f5d66a,#2a2a2a 60%)"></div>
    <h4>Lorem ipsum</h4><p>Lorem ipsum dolor sit amet, conse ctetur adipiscing elit, sed do eiusmod.</p>
  </div>
  <div class="industry" style="left:848px">
    <div class="photo" role="img" aria-label="Hand with pen reviewing business charts" style="background:linear-gradient(160deg,#f0f0f0,#9fb2c8)"></div>
    <h4>Lorem ipsum</h4><p>Lorem ipsum dolor sit amet, conse ctetur adipiscing elit, sed do eiusmod.</p>
  </div>
  <a class="btn-light" href="#">View all industries</a>
</section>

<section class="success">
  <h2 class="section-title heading">Success stories</h2>
  <div class="quote-mark" style="left:140px;top:120px">&ldquo;</div>
  <div class="testimonials">
    <div class="testimonial" style="left:48px">
      <p>Lorem ipsum dolor sit amet, consectetur adipiscing elit, sed do eiusmod tempor incididunt ut labore et dolore magna aliqua. Ut enim ad minim veniam, quis nostrud exercitation ullamco laboris nisi ut aliquip ex ea commodo consequat. Duis aute irure dolor in reprehenderit in voluptate velit esse.</p>
      <div class="author"><span><b>Richard</b><small>Manager</small></span></div>
    </div>
    <div class="testimonial" style="left:472px">
      <p>Lorem ipsum dolor sit amet, consectetur adipiscing elit, sed do eiusmod tempor incididunt ut labore et dolore magna aliqua. Ut enim ad minim veniam, quis nostrud exercitation ullamco laboris nisi ut aliquip ex ea commodo consequat. Duis aute irure dolor in reprehenderit in voluptate velit esse.</p>
      <div class="author"><span><b>Richard</b><small>Manager</small></span></div>
    </div>
  </div>
  <div class="quote-mark" style="left:1000px;top:390px">&rdquo;</div>
  <div class="dots"><i></i><i></i><i class="on"></i><i></i></div>
</section>

<footer class="footer" id="contact">
  <svg class="footer-edge" width="1200" height="24" viewBox="0 0 1200 24" preserveAspectRatio="none"><path d="M0 24V12l40 6 50-10 60 8 45-6 70 9 55-11 60 7 80-8 40 10 70-6 55 8 60-10 45 7 70-5 60 9 50-11 65 8 55-7 70 9 45-6 55 8V24z" fill="#0b0b0b"/></svg>
  <div class="footer-mark"><span>Marwick<br>Partners</span></div>
  <div class="footer-col" style="left:412px">
    <h5>Follow us</h5>
    <div class="follow-item"><i></i><span><em>Like us on</em><br>Friendloop</span></div>
    <div class="follow-item"><i></i><span><em>Follow us on</em><br>Chirpline</span></div>
    <div class="follow-item"><i></i><span><em>Follow us on</em><br>ProLattice</span></div>
  </div>
  <div class="footer-col" style="left:652px">
    <h5>Menu</h5>
    <ul class="menu-list"><li>Home</li><li>About Us</li><li>Services</li><li>Industries</li><li>Our Success</li><li>Contact</li></ul>
  </div>
  <div class="footer-col" style="left:852px">
    <h5>Contact us</h5>
    <div class="contact-item">
      <svg width="30" height="30" viewBox="0 0 30 30"><circle cx="15" cy="15" r="15" fill="#fff"/><path d="M10 8l3 0 1 4-2 1.5c1 2 2.5 3.5 4.5 4.5L18 16l4 1v3c-7 1-13-5-12-12z" fill="#0b0b0b"/></svg>
      <span>Call us<b>800.555.0148</b></span>
    </div>
    <div class="contact-item">
      <svg width="30" height="30" viewBox="0 0 30 30"><circle cx="15" cy="15" r="15" fill="#fff"/><rect x="8" y="10" width="14" height="10" fill="none" stroke="#0b0b0b" stroke-width="1.6"/><path d="M8 10l7 6 7-6" fill="none" stroke="#0b0b0b" stroke-width="1.6"/></svg>
      <span>E-mail us<b>info@marwickpartners.example</b></span>
    </div>
  </div>
  <div class="copyright">Copyright © 2020 All Rights Reserved</div>
</footer>

</body>
</html>
```